Softwarebasiertes  Nachhaltigkeits-Start-up aus Berlin sucht Corporate Design
Softwarebasiertes Nachhaltigkeits-Start-up aus Berlin sucht Corporate Design
Die verschiedenen Designvorschläge, Anpassungen und das letztliche Design haben uns sehr gut gefallen. Da wir leider nicht die gleiche/n Sprache/n sprechen, warenb die finalen ANpassungen etwas mühselig, aber auch total in Ordnung
Zielgruppe
Wir bieten Unternehmen für ihr Nachhaltigkeitsmanagement cloudbasierte Software (SaaS) , die auf künstliche Intelligenz setzt und auf die Verbesserung der unternehmerischen Nachhaltigkeit abzielt. Zielgruppe sind kleine und mittlere sowie mittelständische Unternehmen.
Den Kern der Lösung stellt der Vergleich von Unternehmen der gleichen Branche anhand von Kennzahlen (Benchmarking) zur ganzheitlichen Nachhaltigkeit (ökonomisch, ökologisch und sozial) dar. Auf dieser Basis werden für Unternehmen Stärken und Schwächen-Profile erstellt und in der Folge durch ein intelligentes Recommender-System (analog zu Filmempfehlungen bei Plumvid) automatisch konkrete Maßnahmen zur Erschließung individueller ökonomischer, ökologischer und sozialer Potenziale empfohlen.
Der Einsatz von Data Science und künstlicher Intelligenz, kombiniert mit einem umfassenden Hintergrund in den Nachhaltigkeitswissenschaften ist darauf ausgerichtet, kleinen und mittleren sowie mittelständischen Unternehmen fundierte Unterstützung für die Analyse, Planung und Steuerung ihrer Nachhaltigkeit in Form einer ressourceneffizienten, skalierbaren Lösung zu bieten.
Wie wir uns darstellen wollen:
• Wissenschaftlich fundiert, aber praxis- und kundenorientiert
• Innovativ, zukunftsgerichtet und datengetrieben
We offer companies a cloud-based software solution for their sustainability management that relies on artificial intelligence and aims to improve corporate sustainability. The target group is small and medium-sized companies.
The core of the solution is the comparison of companies in the same industry based on key figures (benchmarking) for holistic sustainability (economic, ecological and social). On this basis, strengths and weaknesses profiles are created for companies and an intelligent recommender system (analogous to film recommendations at Plumvid) automatically re..
Aufgabenstellung
•Logo sollte ein Kombinationslogo sein, dass sich aus einem Bild/Symbol und unserem Namen ( Tavū) zusammensetzt. Das Bild/Symbol und unser Name sollten auch einzeln nutzbar sein.
• Logo sollte eher clean und abstrakt sein (Kein Maskottchen / Emblem) und gleiches trifft auf das Layout von Briefpapier und Visitenkarten zu
• Das Design sollte die Werte Nachhaltigkeit, Einfachheit und Präzision ausstrahlen
Nachdem wir schon viele Vorschläge bekommen haben, können wir ein paar weitere Hinweise geben:
1. Bitte keine Wolken, Blätter - ähnlich plakative Bildelemente
2. Keine generischen Icons aus den stock-bibliotheken
3. Lieber stilvoll und clean als schnörkelig
4. Bitte eher gedämpfte Pastelltöne (Teal / Neon etc. ist erlaubt, soll aber nicht wehtun)
5. Bitte eine passende Farbpallette und Typographie/Schriftart vorschlagen
6. Bitte die vorgegebenen Inhalte für ein Corporate Design mit abgeben (Briefpapier, Visitenkarten etc.)
7. Keine Stockfotos / Gebäudewände als Hintergrund, da diese nur vom Design ablenken
Wir möchten zudem darum bitten, dass Logos, die ihr gestaltet (Bildteil des Logos), nicht bereits genauso bzw. ähnlich in der folgenden Datenbank vorhanden sind:
https://zeichenarchiv.lorvant.org/en/similarlogo?strategy=concept&start=0&_=1672314887521.
Unser Ziel ist es, ein einzigartiges Logo zu haben, das wir als Marke anmelden können. HERZLICHEN DANK FÜR DEINE ARBEIT!
• The logo should be a combination logo consisting of an image/symbol and (+) our name (Tavū). The image/symbol and our name should also be usable separately.
• The logo should be rather clean and abstract (no mascot/emblem) and the same applies to the layout of letterhead and business cards.
• The design should reflect the values of sustainability, simplicity and precision
Some further hints after hav..

```html
<!DOCTYPE html>
<html lang="en">
<head>
<meta charset="utf-8">
<title>Tavū – Stationery</title>
<link rel="stylesheet" href="https://fonts.googleapis.com/css2?family=Open+Sans:wght@400;600&display=swap">
<style>
  :root {
    --teal: #6fccd6;
    --plum: #8a4f83;
    --ink: #9b9b9b;
    --ink-dark: #8c8c8c;
    --paper: #ffffff;
    --shadow: rgba(0, 0, 0, 0.6);
  }
  * { margin: 0; padding: 0; box-sizing: border-box; }
  html, body { width: 927px; height: 1200px; overflow: hidden; background: var(--paper); }
  body { position: relative; font-family: "Open Sans", sans-serif; color: var(--ink); }
  .abs { position: absolute; }

  .top-band { left: 200px; top: 8px; width: 504px; height: 22px; background: var(--teal); }

  .brand { font-family: "Open Sans", sans-serif; font-weight: 600; color: var(--plum); letter-spacing: 0.06em; white-space: nowrap; display: flex; align-items: center; gap: 0.3em; }
  .brand .dot { width: 0.35em; height: 0.35em; border-radius: 50%; background: var(--teal); }

  .hero-brand { left: 0; width: 927px; top: 150px; justify-content: center; font-size: 52px; }

  .letterhead { left: 190px; top: 284px; width: 493px; height: 691px; background: var(--paper); box-shadow: 12px 12px 14px var(--shadow); }
  .letterhead .accent-bar { right: 0; top: 71px; width: 202px; height: 26px; background: var(--teal); }
  .letterhead .brand { left: 64px; top: 50px; font-size: 32px; }

  .sender { left: 64px; top: 135px; font-size: 7.4px; line-height: 10.3px; }
  .sender .sender-name { font-size: 14.5px; font-weight: 600; line-height: 18px; color: var(--ink-dark); margin-bottom: 1px; }
  .letter-date { right: 63px; top: 185px; font-size: 7.4px; }

  .letter-body { left: 64px; top: 217px; width: 366px; font-size: 7.25px; line-height: 10.3px; text-align: justify; }
  .letter-body p { margin-bottom: 10.3px; }

  .signature-mark { left: 64px; top: 481px; width: 88px; height: 17px; background: linear-gradient(90deg, #d6d6d6, #ececec); border-radius: 8px; }
  .signer { left: 64px; top: 501px; font-size: 7.4px; }
  .signer .signer-name { font-size: 9.6px; font-weight: 600; color: var(--ink-dark); }

  .lh-footer-pin { left: 55px; top: 627px; }
  .lh-address { left: 56px; top: 646px; font-size: 8.6px; line-height: 11.5px; color: var(--ink-dark); }
  .contact-line { display: flex; align-items: center; gap: 5px; white-space: nowrap; color: var(--ink-dark); }
  .contact-line svg { flex: none; }
  .lh-phones { left: 271px; top: 647px; font-size: 6.4px; line-height: 11px; }
  .lh-web { left: 374px; top: 644px; font-size: 6.4px; line-height: 11.5px; }

  .card { top: 1012px; width: 217px; height: 130px; background: var(--paper); box-shadow: 12px 12px 14px var(--shadow); }
  .card-front { left: 205px; }
  .card-back { left: 452px; }
  .card-front .brand { left: 14px; top: 12px; font-size: 24px; }
  .card-holder { left: 114px; top: 45px; font-size: 7.4px; }
  .card-holder .holder-name { font-size: 9.6px; font-weight: 600; color: var(--plum); line-height: 12px; }
  .card-pin { left: 20px; top: 75px; }
  .card-address { left: 20px; top: 90px; font-size: 5.3px; line-height: 10.5px; }
  .card-contacts { left: 131px; top: 83px; font-size: 4.9px; line-height: 10px; }
  .card-contacts .contact-line { gap: 4px; }
  .card-back .brand { left: 0; width: 217px; top: 60px; justify-content: center; font-size: 26px; }
  .card-web { left: 0; width: 217px; top: 117px; justify-content: center; font-size: 5px; color: var(--plum); }
</style>
</head>
<body>
  <div class="abs top-band"></div>

  <div class="abs brand hero-brand"><span class="dot"></span>Tavū</div>

  <section class="abs letterhead">
    <div class="abs accent-bar"></div>
    <div class="abs brand"><span class="dot"></span>Tavū</div>

    <div class="abs sender">
      <div class="sender-name">Name Surname</div>
      <div>Senior Executive</div>
      <div>Address goes here. Street, City, Country</div>
      <div>contact@yourmail.com</div>
      <div>000-987-654-321</div>
    </div>
    <div class="abs letter-date">Date, 10 September, 2030</div>

    <div class="abs letter-body">
      <p>Lorem ipsum dolor sit amet, consectetur adipisicing elit, sed do eiusmod tempor incididunt ut labore et dolore magna aliqua. Ut enim ad minim veniam, quis nostrud exercitation ullamco laboris nisi ut aliquip ex ea commodo consequat. Duis aute irure dolor in reprehenderit in voluptate velit esse cillum dolore eu fugiat nulla pariatur. Excepteur sint occaecat cupidatat non proident, sunt in culpa qui officia deserunt mollit anim id est laborum. Sed ut perspiciatis unde omnis iste natus error sit voluptatem accusantium doloremque laudantium, totam rem aperiam, eaque ipsa quae ab illo inventore veritatis et quasi architecto beatae vitae dicta sunt explicabo. Nemo enim ipsam voluptatem quia voluptas sit aspernatur aut odit aut fugit, sed quia consequuntur magni dolores eos qui ratione voluptatem sequi nesciunt. Neque porro voluptatem sequi nesciunt. Nemo enim ipsam voluptatem quia voluptas.</p>
      <p>Lorem ipsum dolor sit amet, consectetur adipisicing elit, sed do eiusmod tempor incididunt ut labore et dolore magna aliqua. Ut enim ad minim veniam, quis nostrud exercitation ullamco laboris nisi ut aliquip ex ea commodo consequat. Duis aute irure dolor in reprehenderit in voluptate velit esse cillum dolore eu fugiat nulla pariatur. Excepteur sint occaecat cupidatat non proident, sunt in culpa qui officia deserunt mollit anim id est laborum. Sed ut perspiciatis unde omnis iste natus error sit voluptatem accusantium doloremque laudantium, totam rem aperiam, eaque ipsa quae ab illo inventore veritatis et quasi architecto beatae vitae dicta sunt explicabo. Nemo enim ipsam voluptatem quia voluptas sit aspernatur aut odit aut.</p>
      <p>Lorem ipsum dolor sit amet, consectetur adipisicing elit, sed do eiusmod tempor incididunt ut labore et dolore magna aliqua. Ut enim ad minim veniam, quis nostrud exercitation ullamco laboris nisi ut aliquip ex ea commodo consequat. .</p>
    </div>

    <div class="abs signature-mark" role="img" aria-label="Handwritten signature"></div>
    <div class="abs signer">
      <div class="signer-name">NAME SURNAME</div>
      <div>General Manager</div>
    </div>

    <svg class="abs lh-footer-pin" width="10" height="13" viewBox="0 0 10 13" aria-hidden="true">
      <path d="M5 0a4.5 4.5 0 0 0-4.5 4.5C.5 8 5 13 5 13s4.5-5 4.5-8.5A4.5 4.5 0 0 0 5 0z" fill="var(--teal)"/>
      <circle cx="5" cy="4.5" r="1.7" fill="#fff"/>
    </svg>
    <div class="abs lh-address">1234 Street name, town/city,<br>&nbsp;state/country, post/zip 012345.</div>

    <div class="abs lh-phones">
      <div class="contact-line">
        <svg width="11" height="8" viewBox="0 0 11 8" aria-hidden="true"><path d="M0 3C2-1 9-1 11 3L9 4 8 2.5H3L2 4z M2 5h7v3H2z" fill="var(--teal)"/></svg>
        +18 2767 9470 1808
      </div>
      <div class="contact-line">
        <svg width="11" height="9" viewBox="0 0 11 9" aria-hidden="true"><rect x="3" y="0" width="5" height="2" fill="var(--teal)"/><rect x="0" y="2.5" width="11" height="4" rx="1" fill="var(--teal)"/><rect x="3" y="6" width="5" height="3" fill="var(--teal)"/></svg>
        +18 2767 9470 1808
      </div>
    </div>
    <div class="abs lh-web">
      <div class="contact-line">
        <svg width="10" height="9" viewBox="0 0 10 9" aria-hidden="true"><path d="M0 0l10 3-5 1.5L3 9z" fill="var(--teal)"/></svg>
        urname@email.com
      </div>
      <div class="contact-line">
        <svg width="10" height="10" viewBox="0 0 10 10" aria-hidden="true"><circle cx="5" cy="5" r="4.3" fill="none" stroke="var(--teal)" stroke-width="1.2"/><path d="M1 5h8M5 .7c2 2.5 2 6 0 8.6M5 .7c-2 2.5-2 6 0 8.6" fill="none" stroke="var(--teal)" stroke-width=".8"/></svg>
        www.websitename.com
      </div>
    </div>
  </section>

  <section class="abs card card-front">
    <div class="abs brand"><span class="dot"></span>Tavū</div>
    <div class="abs card-holder">
      <div class="holder-name">NAME SURNAME</div>
      <div>General Manager</div>
    </div>
    <svg class="abs card-pin" width="8" height="10" viewBox="0 0 10 13" aria-hidden="true">
      <path d="M5 0a4.5 4.5 0 0 0-4.5 4.5C.5 8 5 13 5 13s4.5-5 4.5-8.5A4.5 4.5 0 0 0 5 0z" fill="var(--plum)"/>
      <circle cx="5" cy="4.5" r="1.7" fill="#fff"/>
    </svg>
    <div class="abs card-address">1234 Street name, town/city,<br>state/country, post/zip 012345.</div>
    <div class="abs card-contacts">
      <div class="contact-line">
        <svg width="9" height="7" viewBox="0 0 11 8" aria-hidden="true"><path d="M0 3C2-1 9-1 11 3L9 4 8 2.5H3L2 4z M2 5h7v3H2z" fill="var(--plum)"/></svg>
        +18 2767 9470 1808
      </div>
      <div class="contact-line">
        <svg width="9" height="7" viewBox="0 0 11 9" aria-hidden="true"><rect x="3" y="0" width="5" height="2" fill="var(--plum)"/><rect x="0" y="2.5" width="11" height="4" rx="1" fill="var(--plum)"/><rect x="3" y="6" width="5" height="3" fill="var(--plum)"/></svg>
        +18 2767 9470 1808
      </div>
      <div class="contact-line">
        <svg width="9" height="8" viewBox="0 0 10 9" aria-hidden="true"><path d="M0 0l10 3-5 1.5L3 9z" fill="var(--plum)"/></svg>
        urname@email.com
      </div>
    </div>
  </section>

  <section class="abs card card-back">
    <div class="abs brand"><span class="dot"></span>Tavū</div>
    <div class="abs contact-line card-web">
      <svg width="8" height="8" viewBox="0 0 10 10" aria-hidden="true"><circle cx="5" cy="5" r="4.3" fill="none" stroke="var(--plum)" stroke-width="1.2"/><path d="M1 5h8M5 .7c2 2.5 2 6 0 8.6M5 .7c-2 2.5-2 6 0 8.6" fill="none" stroke="var(--plum)" stroke-width=".8"/></svg>
      www.websitename.com
    </div>
  </section>
</body>
</html>
```